Polystyrene Environmental Synopsis

We need a fact sheet for quick reference that groups information units and has a simple but engaging visual presentation of the text and various infographics. We are a trade association representing polystyrene foam manufacturers and this piece is intended to help our members provide effective messaging to their sales personnel.

To view our typical company design/style please see our website at www.flarenticouncil.org. Our primary RGB colors are: (187,140,9); (94,47,29); (94,138,164); and (164,167,15). Secondary RGB colors are (249,162,28) and (218,210,208). Our title/header font is DIN Next LT Pro and our copy font is Calibri 10.5 pt. We can deviate from the font specification if beneficial.

Target Market(s)

Polystyrene manufacturer plant workers and other employees.

Font styles to use
Sans Serif

Requirements
Must have
• Information presentation must be clean and easy to reference.

```html
<!DOCTYPE html>
<html lang="en">
<head>
<meta charset="utf-8">
<title>EPS Bans – Fact Sheet</title>
<link href="https://fonts.googleapis.com/css2?family=Barlow:wght@500;600&family=Barlow+Semi+Condensed:wght@500;700&display=swap" rel="stylesheet">
<style>
  :root {
    --gold: #bb8c09;
    --brown: #5e2f1d;
    --olive: #a4a70f;
    --olive-soft: #e6e6b8;
    --ink: #1f1a17;
    --paper: #ffffff;
  }
  * { box-sizing: border-box; margin: 0; padding: 0; }
  html, body { width: 850px; height: 1200px; overflow: hidden; background: var(--paper); }
  .sheet { position: relative; width: 850px; height: 1200px; background: var(--paper); overflow: hidden; }

  .top-band {
    position: absolute; left: 0; top: 0; width: 850px; height: 47px;
    background: var(--olive);
    display: flex; align-items: center; justify-content: flex-end; padding-right: 32px;
  }
  .top-band h1 {
    font-family: "Barlow", sans-serif; font-weight: 600; font-size: 19px;
    letter-spacing: 0.5px; color: var(--brown);
  }

  .spine {
    position: absolute; left: 19px; top: 47px; width: 16px; height: 1140px;
    background: var(--gold);
  }

  .section-tab {
    position: absolute; left: 0; width: 256px;
    background: var(--brown);
    border-radius: 0 40px 10px 0;
    box-shadow: 4px 3px 6px rgba(0,0,0,0.25);
    display: flex; align-items: center; justify-content: flex-end;
    padding-right: 14px;
  }
  .section-tab h2 {
    font-family: "Barlow", sans-serif; font-weight: 500; font-size: 24px;
    line-height: 33px; letter-spacing: 1.2px; color: var(--paper);
    text-align: right; text-transform: uppercase;
  }
  .tab-risky { top: 67px; height: 498px; }
  .tab-sustainable { top: 584px; height: 288px; }
  .tab-litter { top: 893px; height: 292px; }

  .icon-slot {
    position: absolute; background: var(--olive-soft); border-radius: 10px;
  }

  .fact {
    position: absolute;
    font-family: "Barlow Semi Condensed", sans-serif; font-weight: 500;
    font-size: 12.5px; line-height: 20.5px; color: var(--ink);
    text-align: center; text-transform: uppercase;
  }
  .fact strong { color: var(--brown); font-weight: 700; }
</style>
</head>
<body>
<main class="sheet">
  <header class="top-band"><h1>EPS BANS</h1></header>
  <div class="spine"></div>

  <section class="section-tab tab-risky"><h2>Material<br>substitutions<br>are risky</h2></section>
  <section class="section-tab tab-sustainable"><h2>EPS is more<br>sustainable<br>than most<br>people<br>imagine</h2></section>
  <section class="section-tab tab-litter"><h2>Litter<br>problems<br>are not<br>material<br>dependent</h2></section>

  <div class="icon-slot" style="left:386px;top:107px;width:96px;height:92px" role="img" aria-label="Icon of a research report with a magnifying glass"></div>
  <p class="fact" style="left:324px;top:222px;width:220px">Recent studies show<br>that <strong>heavier alternatives</strong><br><strong>to lightweight plastics</strong><br><strong>can significantly increase</strong><br><strong>raw material requirements,</strong><br><strong>energy consumption &amp;</strong><br><strong>landfill volume.</strong></p>

  <div class="icon-slot" style="left:626px;top:100px;width:130px;height:71px" role="img" aria-label="Icon of a foam clamshell food container"></div>
  <p class="fact" style="left:581px;top:254px;width:220px">On a <strong>global scale</strong>,<br>environmental costing<br>indicates that plastics<br>alternatives may cost<br><strong>$400 to $500 billion</strong><br>more (4 to 5 times more).</p>

  <div class="icon-slot" style="left:342px;top:382px;width:156px;height:45px" role="img" aria-label="Icon of a steak and a fish"></div>
  <p class="fact" style="left:320px;top:450px;width:200px"><strong>Meat, fish &amp; produce</strong><br><strong>shipped</strong> in EPS have a<br><strong>longer shelf life</strong>,<br>leading <strong>to less food</strong><br><strong>waste</strong></p>

  <div class="icon-slot" style="left:377px;top:612px;width:100px;height:78px" role="img" aria-label="Icon of a low-reading gauge"></div>
  <p class="fact" style="left:344px;top:716px;width:180px">EPS foam is of <strong>98%</strong><br><strong>air</strong>, which results in<br><strong>lower energy</strong><br><strong>consumption.</strong></p>

  <div class="icon-slot" style="left:648px;top:609px;width:92px;height:96px" role="img" aria-label="Icon of a globe with a leaf"></div>
  <p class="fact" style="left:585px;top:716px;width:220px">Life cycle analyses show<br>that EPS has <strong>far less impact</strong><br><strong>on the environment</strong> than<br>other competitive materials<br>for the same use; in<br>particular paper.</p>

  <div class="icon-slot" style="left:382px;top:951px;width:88px;height:74px" role="img" aria-label="Icon of a foam container crossed out"></div>
  <p class="fact" style="left:317px;top:1054px;width:220px">A litter audit in San<br>Francisco <strong>confirmed that</strong><br><strong>a food service ban on</strong><br><strong>polystyrene foam</strong> only<br>changed the type of<br>litter but did not reduce it.</p>

  <div class="icon-slot" style="left:648px;top:940px;width:71px;height:92px" role="img" aria-label="Icon of a person dropping litter"></div>
  <p class="fact" style="left:590px;top:1054px;width:210px"><strong>Improper disposal of</strong><br><strong>any material contributes</strong><br><strong>to litter</strong>, whether it is<br>EPS or another material.</p>
</main>
</body>
</html>
```